Business card design for Corvane Engineering Tandem

We need a new business card design along with all the necessary to place an order. The company is Corvane Engineering Tandem and we recently updated our logo.

```html
<!DOCTYPE html>
<html lang="en">
<head>
<meta charset="utf-8">
<title>Corvane Engineering Tandem – Business Card</title>
<link href="https://fonts.googleapis.com/css2?family=Montserrat:wght@500;600;700&family=Arimo:wght@400&display=swap" rel="stylesheet">
<style>
  :root {
    --page-bg: #c4c4c4;
    --card-white: #ffffff;
    --brand-yellow: #e2bd22;
    --band-grey: #8f8f8f;
    --ink: #1c1c1c;
    --back-light: #8a8a8a;
    --back-dark: #3b3b3b;
  }
  * { box-sizing: border-box; margin: 0; padding: 0; }
  html, body { width: 1200px; height: 800px; overflow: hidden; }
  body {
    background: var(--page-bg);
    display: flex;
    align-items: center;
    justify-content: center;
    gap: 40px;
    font-family: "Arimo", Arial, sans-serif;
  }
  .card {
    position: relative;
    width: 540px;
    height: 309px;
    border-radius: 18px;
    overflow: hidden;
    box-shadow: 0 10px 24px rgba(0,0,0,0.25);
  }
  .card-front { background: var(--card-white); }
  .front-shapes { position: absolute; inset: 0; }
  .holder {
    position: absolute;
    left: 34px;
    top: 58px;
  }
  .holder-name {
    font-family: "Montserrat", sans-serif;
    font-weight: 700;
    font-size: 21px;
    letter-spacing: 0.5px;
    color: var(--brand-yellow);
  }
  .holder-role {
    font-family: "Montserrat", sans-serif;
    font-weight: 500;
    font-size: 12.5px;
    letter-spacing: 0.4px;
    color: var(--ink);
    margin-top: 2px;
  }
  .contact-list {
    position: absolute;
    left: 34px;
    top: 150px;
    list-style: none;
    color: var(--card-white);
    font-size: 14px;
    line-height: 20px;
  }
  .contact-list li { display: flex; align-items: center; gap: 8px; }
  .contact-icon { width: 13px; height: 13px; flex: none; }
  .address {
    position: absolute;
    left: 34px;
    top: 234px;
    font-size: 15px;
    line-height: 20px;
    color: var(--ink);
  }
  .front-wordmark {
    position: absolute;
    right: 34px;
    top: 118px;
    width: 150px;
    text-align: right;
    font-family: "Montserrat", sans-serif;
    font-weight: 600;
    font-size: 17px;
    line-height: 22px;
    color: var(--band-grey);
    text-transform: uppercase;
  }
  .card-back {
    background: linear-gradient(160deg, var(--back-light) 0%, var(--back-dark) 100%);
    display: flex;
    align-items: center;
    justify-content: center;
  }
  .back-wordmark {
    display: flex;
    align-items: center;
    gap: 14px;
  }
  .wordmark-square {
    width: 30px;
    height: 30px;
    background: var(--brand-yellow);
  }
  .wordmark-text {
    font-family: "Montserrat", sans-serif;
    font-weight: 600;
    color: var(--card-white);
    text-transform: uppercase;
    line-height: 1.1;
  }
  .wordmark-main { font-size: 44px; letter-spacing: 4px; }
  .wordmark-sub { font-size: 17px; letter-spacing: 2px; }
</style>
</head>
<body>

<section class="card card-front">
  <svg class="front-shapes" width="540" height="309" viewBox="0 0 540 309">
    <polygon points="345,72 435,0 540,0 540,16 470,72" fill="var(--brand-yellow)"/>
    <polygon points="0,145 330,145 290,222 0,222" fill="var(--band-grey)"/>
  </svg>

  <div class="holder">
    <p class="holder-name">DANIEL HARLOW</p>
    <p class="holder-role">MANAGING DIRECTOR</p>
  </div>

  <ul class="contact-list">
    <li>
      <svg class="contact-icon" viewBox="0 0 16 16"><path d="M4 1l3 3-2 2c1 2 3 4 5 5l2-2 3 3-2 3C7 15 1 9 1 3z" fill="var(--brand-yellow)"/></svg>
      044-987 654 321
    </li>
    <li>
      <svg class="contact-icon" viewBox="0 0 16 16"><rect x="1" y="3" width="14" height="10" fill="var(--brand-yellow)"/><path d="M1 3l7 6 7-6" stroke="var(--band-grey)" stroke-width="1.4" fill="none"/></svg>
      info@corvanetandem.com
    </li>
    <li>
      <svg class="contact-icon" viewBox="0 0 16 16"><circle cx="8" cy="8" r="7" fill="var(--brand-yellow)"/><path d="M1 8h14M8 1v14M3 4h10M3 12h10" stroke="var(--band-grey)" stroke-width="1"/></svg>
      www.corvanetandem.com
    </li>
  </ul>

  <p class="address">421, Address line goes here<br>45452, Country Name</p>

  <p class="front-wordmark">Corvane Engineering Tandem</p>
</section>

<section class="card card-back">
  <div class="back-wordmark">
    <span class="wordmark-square"></span>
    <div class="wordmark-text">
      <p class="wordmark-main">Corvane</p>
      <p class="wordmark-sub">Engineering Tandem</p>
    </div>
  </div>
</section>

</body>
</html>
```